Mortgage and Asset Finance Broker Needs a Wordpress Website Design

I need a modern looking Wordpress website to showcase my service as a mortgage and asset broker. I have a company and we work with various lenders to arrange mortgages, as well as commercial lending and business asset finance. The website needs to look professional, be easy to navigate and capture leads. SEO is obviously very important to me. It really needs to be something that shows trust and professioanlism.
Updates

On the home page I will need to have some boxes for Home Loans, Refinancing, Business (and Agriculture) Loans etc. I'd like a carousel in the middle which shows our lenders (so that can have the banks logos added).

It needs to be easy top navigate and showcase all we do - Home Loans, Refinancing, Commercial Loans, Car Loans, Asset Finance etc.

There are plenty of companies on the internet that do this.

There is some good information here https://lendplatehq.com.au/mortgage-broker-homepage/

I need to make sure that editing the website is easy (I think Wordpress has something that allows that).

Also we are very much an Australian business so that is something to advertise.

Industry/Entity Type

Mortgage and Finance Broker

Coding

Coded - Design and coding required

Number of Pages Required

5+ page

Requirements
Must have
• Easy to navigate professional feel. Must be responsive and mobile friendly.
Nice to have
• Homepage with links to inner pages. Contact buttons.

```html
<!DOCTYPE html>
<html lang="en">
<head>
<meta charset="utf-8">
<title>Vantora Financial Services</title>
<link href="https://fonts.googleapis.com/css2?family=Poppins:wght@400;500;600;700;800&display=swap" rel="stylesheet">
<style>
:root{
  --blue:#0f5fae;
  --blue-dark:#0b4f94;
  --orange:#f7901e;
  --ink:#2b2b2b;
  --text:#444;
  --grey-bg:#e9e8ea;
  --footer:#232323;
  --white:#fff;
}
*{box-sizing:border-box;margin:0;padding:0}
html,body{width:1200px;height:3208px;overflow:hidden}
body{font-family:"Poppins",sans-serif;color:var(--text);background:var(--white);position:relative}
a{text-decoration:none;color:inherit}
.abs{position:absolute}

/* header */
.site-header{position:absolute;left:0;top:0;width:1200px;height:88px;background:var(--white);border-bottom:1px solid #e4e4e4}
.brand{position:absolute;left:112px;top:24px;display:flex;align-items:center;gap:8px;font-weight:700;font-size:30px;color:var(--ink)}
.brand .dot{width:16px;height:16px;background:var(--orange)}
.main-nav{position:absolute;left:427px;top:34px;display:flex;gap:41px;font-size:15px;color:#333}
.main-nav .active{color:var(--blue);font-weight:600}
.btn-apply{position:absolute;display:flex;align-items:center;justify-content:center;color:var(--white);font-size:15px;background:linear-gradient(135deg,var(--blue) 78%,var(--orange) 78%)}
.btn-apply.header-cta{left:915px;top:25px;width:173px;height:46px}

/* hero */
.hero{position:absolute;left:0;top:88px;width:1200px;height:592px;
  background:
    radial-gradient(ellipse 420px 300px at 860px 260px,rgba(240,220,200,.55),transparent 70%),
    radial-gradient(ellipse 380px 260px at 1050px 460px,rgba(120,160,205,.55),transparent 70%),
    linear-gradient(90deg,#1d4a7c 0%,#2f5f91 30%,#6f8fae 55%,#a9a49a 75%,#c8b7a3 100%)}
.hero-copy{position:absolute;left:112px;top:100px;width:520px}
.hero-copy h1{font-size:51px;line-height:62px;color:var(--orange);font-weight:700}
.hero-copy p{margin-top:22px;width:505px;font-size:15px;line-height:23px;color:var(--white)}
.btn-solid{display:inline-flex;align-items:center;justify-content:center;background:var(--blue);color:var(--white);font-size:15px}
.hero-copy .btn-solid{margin-top:36px;width:144px;height:48px}

/* about */
.about-photo{left:112px;top:753px;width:418px;height:320px;
  background:radial-gradient(ellipse 160px 140px at 220px 120px,rgba(235,235,235,.7),transparent 70%),
  linear-gradient(135deg,#3f5670 0%,#8da2b6 45%,#c7d1da 60%,#5d6c7c 100%)}
.years-badge{left:427px;top:976px;width:141px;height:118px;background:var(--blue);border-radius:4px;color:var(--white);text-align:center;padding-top:10px}
.years-badge strong{display:block;font-size:46px;line-height:50px;color:var(--orange);font-weight:700}
.years-badge span{font-size:13px;font-weight:600;line-height:19px;display:block}
.eyebrow{display:flex;align-items:center;gap:16px;font-size:16px;font-weight:600;color:var(--blue)}
.eyebrow::before{content:"";width:46px;height:3px;background:var(--blue)}
.eyebrow.center::after{content:"";width:34px;height:3px;background:var(--blue)}
.eyebrow.center::before{width:34px}
.about-copy{left:612px;top:755px;width:460px}
.about-copy h2{margin-top:14px;font-size:33px;line-height:43px;color:var(--ink);font-weight:600;width:460px}
.about-copy p{margin-top:14px;width:445px;font-size:15px;line-height:26px;color:#333}
.about-copy p+p{margin-top:6px}

/* services */
.services-head{left:112px;top:1166px}
.section-title{font-size:32px;font-weight:600;color:var(--ink)}
.services-head .section-title{margin-top:16px}
.btn-apply.view-more{left:915px;top:1186px;width:173px;height:45px}
.service-card{position:absolute;top:1290px;width:289px}
.service-card .rule{margin-left:38px;width:168px;height:2px;background:var(--blue)}
.service-card h3{margin:20px 0 0 23px;font-size:17px;font-weight:600;color:var(--ink)}
.service-card p{margin:12px 0 0 23px;width:250px;font-size:15px;line-height:25px;color:#555}
.read-more{display:inline-flex;align-items:center;gap:4px;font-size:15px;font-weight:600;color:var(--blue)}
.service-card .read-more{margin:8px 0 0 20px}
.service-photo{margin-top:14px;width:289px;height:173px;position:relative}
.service-photo .icon-tile{position:absolute;right:17px;bottom:19px;width:57px;height:53px;background:var(--blue);border:2px solid var(--white);display:flex;align-items:center;justify-content:center}

/* lenders */
.lenders{left:0;top:1640px;width:1200px;height:548px}
.lenders-title{left:0;top:1742px;width:1200px;text-align:center;font-size:31px;font-weight:600;color:var(--blue)}
.lenders-sub{left:300px;top:1796px;width:600px;text-align:center;font-size:15px;line-height:25px;color:#444}
.hr{height:2px;background:#b9c8d8}
.lender-logo{top:1941px;width:148px;height:132px;background:var(--white);display:flex;align-items:center;justify-content:center;gap:6px;font-size:13px;font-weight:600;color:var(--blue)}
.lender-logo i{width:12px;height:12px;background:var(--orange);display:block}
.carousel-arrow{top:1988px}

/* blog */
.blog-head{left:0;top:2248px;width:1200px;display:flex;flex-direction:column;align-items:center}
.blog-head .section-title{margin-top:16px}
.post-card{position:absolute;top:2385px;width:298px;height:357px;background:var(--blue);border-radius:6px;overflow:hidden;text-align:center;color:var(--white)}
.post-photo{height:180px;border:1px solid var(--white)}
.post-date{position:absolute;left:50%;top:163px;transform:translateX(-50%);background:var(--orange);color:var(--white);font-size:13px;padding:5px 14px;border-radius:16px;white-space:nowrap;display:flex;align-items:center;gap:6px}
.post-card h3{margin:30px 18px 0;font-size:16.5px;line-height:22px;font-weight:700}
.post-card p{margin:4px 28px 0;font-size:15px;line-height:25px;color:#e8eef7}
.post-card .read-more{color:var(--white);margin-top:10px}

/* footer */
.site-footer{left:0;top:2808px;width:1200px;height:400px;background:var(--footer);color:var(--white)}
.footer-brand{left:112px;top:2868px;font-size:32px;font-weight:700;display:flex;align-items:center;gap:8px}
.footer-brand .dot{width:16px;height:16px;background:var(--orange)}
.contact-item{display:flex;align-items:center;gap:14px}
.contact-item small{display:block;font-size:17px}
.contact-item strong{display:block;font-size:15px;font-weight:700}
.footer-col h4{font-size:17px;font-weight:600;color:var(--orange);margin-bottom:8px;line-height:26px}
.footer-col p{font-size:15px;line-height:25px}
.footer-links{list-style:none;font-size:15px;line-height:32px}
.footer-links li::before{content:"↗";color:var(--orange);margin-right:6px}
.latest{display:flex;gap:12px;margin-bottom:12px}
.latest .thumb{width:70px;height:46px;background:linear-gradient(135deg,#4e6c8c,#b5c3d1 55%,#6a7d90)}
.latest span{display:block;font-size:16px}
.latest em{font-style:normal;font-size:14px;color:var(--orange)}
.footer-rule{left:0;top:3165px;width:1200px;height:1px;background:#555}
.copyright{left:0;top:3180px;width:1200px;text-align:center;font-size:14px}
.copyright b{font-weight:400;color:var(--orange)}
</style>
</head>
<body>

<header class="site-header">
  <div class="brand"><span class="dot"></span>Vantora</div>
  <nav class="main-nav">
    <a class="active" href="#">Home</a><a href="#">About Us</a><a href="#">Services</a><a href="#">Blog</a><a href="#">Contact Us</a>
  </nav>
  <a class="btn-apply header-cta" href="#">APPLY NOW</a>
</header>

<section class="hero" role="img" aria-label="Smiling couple sitting on a living room floor with a tablet">
  <div class="hero-copy">
    <h1>Our Loans Will Make Your Dreams Come True</h1>
    <p>It looks like you're looking for more general information on loans.<br>A loan is essentially a sum of money that is borrowed and<br>expected to be paid back with interest over a set period of time.</p>
    <a class="btn-solid" href="#">OUR SERVICES</a>
  </div>
</section>

<div class="abs about-photo" role="img" aria-label="Business team meeting around a table in a bright office"></div>
<div class="abs years-badge"><strong>25</strong><span>Years Of<br>Experience</span></div>
<div class="abs about-copy">
  <div class="eyebrow">WELCOME TO VANTORA</div>
  <h2>We have been working very<br>efficiently with loan.</h2>
  <p>Are you looking for information on home loans? If so, I can help explain the different types, eligibility requirements, and how they work. There are various options, like conventional loans, FHA loans, VA loans, and others. What would you like to know more about?</p>
  <p>There are various options, like conventional loans, FHA loans, VA loans, and others. What would you like to know more about?</p>
</div>

<div class="abs services-head">
  <div class="eyebrow">What We Do</div>
  <h2 class="section-title">Professional Services</h2>
</div>
<a class="btn-apply view-more" href="#">VIEW MORE</a>

<article class="service-card" style="left:112px">
  <div class="rule"></div>
  <h3>Home Loans</h3>
  <p>A home loan, also known as a mortgage, is a loan taken out to</p>
  <a class="read-more" href="#">Read More →</a>
  <div class="service-photo" role="img" aria-label="Hands holding a model house beside small homes" style="background:radial-gradient(ellipse 90px 70px at 150px 60px,rgba(220,90,70,.35),transparent 70%),linear-gradient(120deg,#f0efed 0%,#ddd6cc 45%,#b9aa98 70%,#2f3033 100%)">
    <span class="icon-tile"><svg width="32" height="30" viewBox="0 0 32 30" fill="none" stroke="#fff" stroke-width="1.8"><path d="M3 14 L16 3 L29 14"/><path d="M7 11 V27 H25 V11"/><circle cx="16" cy="18" r="5"/><path d="M16 15.5 V20.5 M14.5 16.8 H17 M15 19.2 H17.5"/></svg></span>
  </div>
</article>
<article class="service-card" style="left:455px">
  <div class="rule"></div>
  <h3>Commercial Loans</h3>
  <p>A commercial loan is a loan specifically designed to finance</p>
  <a class="read-more" href="#">Read More →</a>
  <div class="service-photo" role="img" aria-label="Person signing loan paperwork at a desk" style="background:radial-gradient(ellipse 110px 80px at 140px 70px,rgba(245,245,245,.8),transparent 70%),linear-gradient(135deg,#5f7387 0%,#b9c3cc 40%,#e3e6e9 60%,#8f9aa5 100%)">
    <span class="icon-tile"><svg width="32" height="30" viewBox="0 0 32 30" fill="none" stroke="#fff" stroke-width="1.8"><circle cx="16" cy="15" r="11"/><path d="M16 8 V15 L21 18"/><circle cx="9" cy="22" r="4" fill="#0f5fae"/><path d="M9 20 V24"/></svg></span>
  </div>
</article>
<article class="service-card" style="left:798px">
  <div class="rule"></div>
  <h3>Business Loans</h3>
  <p>Are you looking for information on how to apply for a business</p>
  <a class="read-more" href="#">Read More →</a>
  <div class="service-photo" role="img" aria-label="Three colleagues reviewing a laptop together" style="background:radial-gradient(ellipse 120px 80px at 140px 80px,rgba(240,232,222,.8),transparent 70%),linear-gradient(135deg,#a89682 0%,#d8d2c9 45%,#8494a8 75%,#4f6680 100%)">
    <span class="icon-tile"><svg width="30" height="30" viewBox="0 0 30 30" fill="none" stroke="#fff" stroke-width="1.8"><rect x="5" y="3" width="18" height="24"/><path d="M9 10 H19 M9 15 H19 M9 20 H15"/><path d="M20 24 L27 13"/></svg></span>
  </div>
</article>

<svg class="abs lenders" viewBox="0 0 1200 548" aria-hidden="true"><path d="M0 72 C250 20 420 60 620 70 C860 82 1000 50 1200 25 L1200 548 L0 548 Z" fill="#e9e8ea"/></svg>
<h2 class="abs lenders-title">Our Lenders</h2>
<p class="abs lenders-sub">It sounds like you're referring to a group or organization you are involved with, possibly your own business or network of lenders.</p>
<div class="abs hr" style="left:111px;top:1900px;width:977px"></div>
<div class="abs lender-logo" style="left:111px"><i></i>Harbour Bank</div>
<div class="abs lender-logo" style="left:318px"><i></i>Southgate</div>
<div class="abs lender-logo" style="left:525px"><i></i>Coastline</div>
<div class="abs lender-logo" style="left:733px"><i></i>Meridian</div>
<div class="abs lender-logo" style="left:940px"><i></i>Redgum Credit</div>
<svg class="abs carousel-arrow" style="left:47px" width="36" height="36" viewBox="0 0 36 36"><circle cx="18" cy="18" r="16" fill="none" stroke="#0f5fae" stroke-width="2.5"/><path d="M21 10 L13 18 L21 26" fill="none" stroke="#0f5fae" stroke-width="2.5"/></svg>
<svg class="abs carousel-arrow" style="left:1110px" width="36" height="36" viewBox="0 0 36 36"><circle cx="18" cy="18" r="16" fill="none" stroke="#0f5fae" stroke-width="2.5"/><path d="M15 10 L23 18 L15 26" fill="none" stroke="#0f5fae" stroke-width="2.5"/></svg>
<div class="abs hr" style="left:111px;top:2110px;width:977px"></div>

<div class="abs blog-head">
  <div class="eyebrow center">News &amp; Updates</div>
  <h2 class="section-title">Latest From Our Blog</h2>
</div>

<article class="post-card" style="left:111px">
  <div class="post-photo" role="img" aria-label="Business handshake over a desk" style="background:radial-gradient(ellipse 120px 60px at 150px 110px,rgba(225,230,238,.6),transparent 70%),linear-gradient(160deg,#1f3550 0%,#5a7591 50%,#c9d3de 100%)"></div>
  <span class="post-date"><svg width="12" height="12" viewBox="0 0 12 12" fill="none" stroke="#fff" stroke-width="1.2"><rect x="1" y="2" width="10" height="9"/><path d="M1 5 H11 M4 1 V3 M8 1 V3"/></svg>April 19, 2025</span>
  <h3>1. Your company's blog about loans</h3>
  <p>You might want help writing or managing blog content about</p>
  <a class="read-more" href="#">Read More →</a>
</article>
<article class="post-card" style="left:452px">
  <div class="post-photo" role="img" aria-label="Team discussion around a laptop in an office" style="background:radial-gradient(ellipse 110px 70px at 150px 90px,rgba(210,190,170,.55),transparent 70%),linear-gradient(160deg,#1c2c40 0%,#47627e 50%,#9fb3c6 100%)"></div>
  <span class="post-date"><svg width="12" height="12" viewBox="0 0 12 12" fill="none" stroke="#fff" stroke-width="1.2"><rect x="1" y="2" width="10" height="9"/><path d="M1 5 H11 M4 1 V3 M8 1 V3"/></svg>April 01, 2025</span>
  <h3 style="margin-top:40px">2. Recent blogs on loan topics</h3>
  <p>You need suggestions or summaries of blogs related to</p>
  <a class="read-more" href="#">Read More →</a>
</article>
<article class="post-card" style="left:793px">
  <div class="post-photo" role="img" aria-label="Calculator and documents on a desk" style="background:radial-gradient(ellipse 120px 70px at 190px 110px,rgba(245,245,245,.7),transparent 70%),linear-gradient(150deg,#2e2e30 0%,#6f6f72 45%,#d6d6d6 100%)"></div>
  <span class="post-date"><svg width="12" height="12" viewBox="0 0 12 12" fill="none" stroke="#fff" stroke-width="1.2"><rect x="1" y="2" width="10" height="9"/><path d="M1 5 H11 M4 1 V3 M8 1 V3"/></svg>April 08, 2025</span>
  <h3>3. How to Improve Your Credit Score to Qualify for a Loan</h3>
  <p>Share tips on how businesses or individuals can boost their</p>
  <a class="read-more" href="#">Read More →</a>
</article>

<footer class="abs site-footer"></footer>
<div class="abs footer-brand" style="color:#fff"><span class="dot"></span>Vantora</div>
<div class="abs contact-item" style="left:393px;top:2860px;color:#fff">
  <svg width="24" height="32" viewBox="0 0 24 32"><path d="M12 1C6 1 1.5 5.5 1.5 11.5 1.5 19 12 31 12 31s10.5-12 10.5-19.5C22.5 5.5 18 1 12 1z" fill="#f7901e"/><circle cx="12" cy="11.5" r="4" fill="#232323"/></svg>
  <div><small>Location</small><strong>12 Wattle Street, Parramatta NSW</strong></div>
</div>
<div class="abs contact-item" style="left:927px;top:2868px;color:#fff">
  <svg width="26" height="26" viewBox="0 0 24 24"><path d="M6.6 10.8a15 15 0 0 0 6.6 6.6l2.2-2.2c.3-.3.7-.4 1-.2 1.1.4 2.3.6 3.6.6.6 0 1 .4 1 1V20c0 .6-.4 1-1 1A17 17 0 0 1 3 4c0-.6.4-1 1-1h3.5c.6 0 1 .4 1 1 0 1.3.2 2.5.6 3.6.1.3 0 .7-.2 1z" fill="#f7901e"/></svg>
  <div><small>Call Us</small><strong>0400-123-456</strong></div>
</div>
<div class="abs footer-col" style="left:110px;top:2955px;width:210px;color:#fff">
  <h4>About</h4>
  <p>Financial loans play a crucial role in personal and business finance. They provide access to capital business,</p>
</div>
<div class="abs footer-col" style="left:371px;top:2955px;color:#fff">
  <h4>Quick Links</h4>
  <ul class="footer-links"><li>Home</li><li>About Us</li><li>Services</li><li>Blog</li><li>Contact Us</li></ul>
</div>
<div class="abs footer-col" style="left:529px;top:2989px;color:#fff">
  <ul class="footer-links"><li>Apply Now</li><li>Services</li><li>FAQ</li><li>Terms &amp; Conditions</li><li>Privacy Policy</li></ul>
</div>
<div class="abs footer-col" style="left:742px;top:2955px;color:#fff">
  <h4>Latest Posts</h4>
  <div class="latest"><div class="thumb" role="img" aria-label="Office meeting thumbnail"></div><div><span>Your company's blog about loans</span><em>April 21, 2025</em></div></div>
  <div class="latest"><div class="thumb" role="img" aria-label="Handshake thumbnail"></div><div><span>Recent blogs on loan topics</span><em>April 09, 2025</em></div></div>
</div>
<div class="abs footer-rule"></div>
<p class="abs copyright" style="color:#fff">© Copyright 2025 By <b>Vantora</b> &nbsp;- All rights reserved</p>

</body>
</html>
```